Fernhale Business Card Design

We are looking for a fresh business card design for our new logo. We would like a business card that is unique but friendly. We are in the window coverings business offering blinds, shutters and shades for homes.

Target Market(s)

Targeting the end-consumer

Industry/Entity Type

Business

Requirements
Must have
• Must have a dedicates space for a photo of our sales person. Must contain our new logo (attached).

```html
<!DOCTYPE html>
<html lang="en">
<head>
<meta charset="utf-8">
<title>Fernhale Business Card</title>
<link href="https://fonts.googleapis.com/css2?family=Poppins:wght@400;500;600&display=swap" rel="stylesheet">
<style>
  :root {
    --green: #8bc43f;
    --ink: #55575b;
    --ink-soft: #7a7c80;
    --paper: #ffffff;
    --stage: #e6e6e3;
    --photo-light: #f4f2f0;
    --photo-dark: #3a3837;
  }
  * { box-sizing: border-box; margin: 0; padding: 0; }
  html, body { width: 1200px; height: 930px; overflow: hidden; }
  body {
    background: var(--stage);
    font-family: "Poppins", sans-serif;
    position: relative;
  }
  .card {
    position: absolute;
    left: 240px;
    width: 720px;
    height: 410px;
    border-radius: 22px;
    overflow: hidden;
    box-shadow: 0 6px 18px rgba(0,0,0,0.18);
  }
  /* Front */
  .card-front { top: 40px; background: var(--green); color: var(--paper); }
  .front-brand {
    position: absolute; left: 0; right: 0; top: 160px;
    display: flex; align-items: center; justify-content: center; gap: 22px;
  }
  .brand-square {
    width: 70px; height: 70px; border: 5px solid currentColor; border-radius: 12px;
  }
  .brand-name { font-size: 68px; font-weight: 500; letter-spacing: 1px; line-height: 1; }
  .front-web {
    position: absolute; left: 0; right: 0; bottom: 34px;
    text-align: center; font-size: 15px; letter-spacing: 0.5px;
  }
  /* Back */
  .card-back { top: 480px; background: var(--paper); }
  .back-brand {
    position: absolute; left: 48px; top: 70px;
    display: flex; align-items: center; gap: 18px; color: var(--ink);
  }
  .back-brand .brand-square { width: 58px; height: 58px; border-width: 4px; border-radius: 10px; }
  .back-brand .brand-name { font-size: 50px; }
  .person { position: absolute; left: 48px; top: 176px; }
  .person-name { color: var(--green); font-size: 22px; font-weight: 600; letter-spacing: 1px; text-transform: uppercase; }
  .person-title { color: var(--ink-soft); font-size: 15px; letter-spacing: 1px; text-transform: uppercase; }
  .contacts { position: absolute; left: 48px; top: 244px; list-style: none; }
  .contacts li {
    display: flex; align-items: center; gap: 12px;
    font-size: 15px; color: var(--ink); line-height: 22px;
  }
  .contacts svg { width: 14px; height: 14px; fill: var(--green); flex: none; }
  .photo {
    position: absolute; right: 0; top: 0; width: 300px; height: 370px;
    background: radial-gradient(ellipse at 55% 55%, var(--photo-dark) 0%, #6a6664 45%, var(--photo-light) 80%);
  }
  .address-band {
    position: absolute; left: 0; right: 0; bottom: 0; height: 40px;
    background: var(--green); color: var(--paper);
    font-size: 15px; padding-left: 48px; display: flex; align-items: center;
  }
</style>
</head>
<body>
  <section class="card card-front">
    <div class="front-brand">
      <span class="brand-square"></span>
      <span class="brand-name">Fernhale</span>
    </div>
    <p class="front-web">www.fernhaleliving.com</p>
  </section>

  <section class="card card-back">
    <div class="back-brand">
      <span class="brand-square"></span>
      <span class="brand-name">Fernhale</span>
    </div>
    <div class="person">
      <p class="person-name">Dana Whitlock</p>
      <p class="person-title">Realtor</p>
    </div>
    <ul class="contacts">
      <li><svg viewBox="0 0 24 24"><path d="M6.6 10.8a15 15 0 0 0 6.6 6.6l2.2-2.2a1 1 0 0 1 1-.25 11.4 11.4 0 0 0 3.6.57 1 1 0 0 1 1 1V20a1 1 0 0 1-1 1A17 17 0 0 1 3 4a1 1 0 0 1 1-1h3.5a1 1 0 0 1 1 1c0 1.25.2 2.45.57 3.57a1 1 0 0 1-.25 1z"/></svg>(014) 552-0187</li>
      <li><svg viewBox="0 0 24 24"><path d="M7 1h10a2 2 0 0 1 2 2v18a2 2 0 0 1-2 2H7a2 2 0 0 1-2-2V3a2 2 0 0 1 2-2zm0 3v14h10V4z"/></svg>(014) 552-0187</li>
      <li><svg viewBox="0 0 24 24"><path d="M6 2h12v6H6zM4 9h16a2 2 0 0 1 2 2v7h-4v4H6v-4H2v-7a2 2 0 0 1 2-2zm4 7v4h8v-4z"/></svg>(014) 552-0187</li>
      <li><svg viewBox="0 0 24 24"><path d="M2 5h20v14H2zm2 2v.5l8 5 8-5V7z"/></svg>info@fernhaleblinds.com</li>
      <li><svg viewBox="0 0 24 24"><path d="M12 2a10 10 0 1 0 0 20 10 10 0 0 0 0-20zm0 2c.9 1.2 1.6 2.6 2 4h-4c.4-1.4 1.1-2.8 2-4zM4.3 14a8 8 0 0 1 0-4h3.4a16 16 0 0 0 0 4zm5.7 0a14 14 0 0 1 0-4h4a14 14 0 0 1 0 4zm6.3 0a16 16 0 0 0 0-4h3.4a8 8 0 0 1 0 4zM10 16h4c-.4 1.4-1.1 2.8-2 4-.9-1.2-1.6-2.6-2-4z"/></svg>www.fernhaleblinds.com</li>
    </ul>
    <div class="photo" role="img" aria-label="Portrait photo of the sales person"></div>
    <p class="address-band">P.O.Box: 248, Harbour Street, Lakeview</p>
  </section>
</body>
</html>
```